Business Card Design Project

Business Card design based on logo.
Updates

I need business card, letterhead, envelope, and if possible, Powerpoint slide template.

On front of business card: Just logo- and  my name and title:  Harriet Lindqvist, Principal

On reverse-logo and the rest of the contact info:

4871 Quarry Lane
Davis, CA 95618
650-318-2764
hl@brackenstudyworks.example

On letterhead-Just logo at top, at bottom  the rest-very small along the bottom

On PPT slide-just the logo.

I also want to try a few other colors-I like lime/dark grey (not black) but would like to try Sienna, maybe also indigo or bright blue-green.

I forgot to add-

On the business card-switch to vertical on reverse side and put:

Reverse side-switch to vertical and list:

Harriet Lindqvist
Principal
Bracken Study Works, LLC

650-318-2764

4871 Quarry Lane
Davis, CA 95618

Harriet Lindqvist
Principal

650-318-2764

4871 Quarry Lane
Davis, CA 95618

I have another project at the same time-for Stationery. Feel free to submit to that one also.

That one includes letterhead, envelope, PPT slide, folder cover sheet-HL

Industry/Entity Type

Business

Requirements
Must have
• Must use logo-preferably lime green version-with gray, not black or just 2-tone -logo on colored background.

```html
<!DOCTYPE html>
<html lang="en">
<head>
<meta charset="utf-8">
<title>Bracken Study Works — Business Card</title>
<link rel="stylesheet" href="https://fonts.googleapis.com/css2?family=Open+Sans:wght@400;600&display=swap">
<style>
  :root {
    --backdrop: #2b2b2b;
    --card: #ffffff;
    --lime: #8db33a;
    --slate: #4a4a4c;
    --ink: #3f3f41;
    --paper-text: #f2f2f2;
  }
  * { margin: 0; padding: 0; box-sizing: border-box; }
  html, body { width: 1200px; height: 722px; overflow: hidden; }
  body {
    background: var(--backdrop);
    font-family: "Open Sans", Arial, sans-serif;
    position: relative;
  }
  .card {
    position: absolute;
    top: 99px;
    width: 300px;
    height: 524px;
    border-radius: 14px;
    background: var(--card);
    overflow: hidden;
  }
  .card--front { left: 293px; }
  .card--back { left: 607px; }

  .brand {
    position: absolute;
    left: 0; right: 0;
    text-align: center;
  }
  .brand__mark {
    display: block;
    width: 22px; height: 22px;
    margin: 0 auto 18px;
    background: var(--lime);
  }
  .brand__name {
    font-weight: 400;
    color: var(--slate);
    letter-spacing: 6px;
    line-height: 1.25;
    font-size: 30px;
  }
  .card--front .brand { top: 168px; }
  .card--back .brand { top: 92px; }

  .website {
    position: absolute;
    left: 0; right: 0;
    bottom: 40px;
    text-align: center;
    font-size: 13px;
    letter-spacing: 1px;
    color: var(--ink);
  }
  .website__domain { color: var(--lime); }

  .contact-panel {
    position: absolute;
    left: 0; right: 0;
    top: 283px;
    bottom: 0;
    background: var(--slate);
    border-top: 3px solid var(--lime);
    box-shadow: 0 -2px 0 #ffffff, 0 -3px 0 #d8d8d8;
    padding: 54px 0 0 33px;
    color: var(--paper-text);
  }
  .holder { font-size: 16px; font-weight: 600; color: var(--lime); }
  .holder__title { font-size: 13px; font-weight: 400; color: var(--paper-text); }
  .contact-list { list-style: none; margin-top: 22px; font-size: 13px; }
  .contact-list li { display: flex; align-items: center; height: 21px; }
  .contact-list svg { width: 11px; height: 11px; margin-right: 7px; fill: var(--lime); }
  .company { margin-top: 20px; font-size: 14px; font-weight: 600; color: var(--lime); }
  .address { margin-top: 5px; font-size: 13px; }
</style>
</head>
<body>
  <section class="card card--front">
    <div class="brand">
      <span class="brand__mark"></span>
      <p class="brand__name">BRACKEN<br>STUDY WORKS</p>
    </div>
    <p class="website">www.<span class="website__domain">brackenstudyworks</span>.example</p>
  </section>

  <section class="card card--back">
    <div class="brand">
      <span class="brand__mark"></span>
      <p class="brand__name">BRACKEN<br>STUDY WORKS</p>
    </div>
    <div class="contact-panel">
      <p class="holder">Harriet Lindqvist, <span class="holder__title">Principal</span></p>
      <ul class="contact-list">
        <li>
          <svg viewBox="0 0 24 24" aria-hidden="true"><path d="M6.6 10.8c1.4 2.8 3.8 5.1 6.6 6.6l2.2-2.2c.3-.3.7-.4 1-.2 1.1.4 2.3.6 3.6.6.6 0 1 .4 1 1V20c0 .6-.4 1-1 1C10.6 21 3 13.4 3 4c0-.6.4-1 1-1h3.5c.6 0 1 .4 1 1 0 1.3.2 2.5.6 3.6.1.3 0 .7-.2 1z"/></svg>
          650-318-2764
        </li>
        <li>
          <svg viewBox="0 0 24 24" aria-hidden="true"><path d="M2 5h20v14H2z M4 7v.5l8 5 8-5V7l-8 5z" fill-rule="evenodd"/></svg>
          hl@brackenstudyworks.example
        </li>
      </ul>
      <p class="company">Bracken Study Works, LLC</p>
      <p class="address">4871 Quarry Lane Davis, CA 95618</p>
    </div>
  </section>
</body>
</html>
```